Mortgage Protection Insurance Flyer

The target audience are new home owners so the design needs to be clean and simple.

This a primarily for Final Expense Insurance, but need an area where it says "We Also Specialize In:"
- Medicare Supplement Insurance (MediGap)
- Annuities
- Final Expense

All flyer versions need to be editable. Colors to be used are red, white or black. Refer to my website for colors and photos (corvantshield.com). Will attach my logo and a flyer that I found online that is the format that I am looking for (for 8.5 in. x 11 in version). Need flyer in standard letter size 8.5 in. x11 in. but also in 8.5 in. x 5.5 in and 5.0 in. x 8.0 in. All sizes to be portrait oriented. If picked as winning design, need all flyer versions in full color, also in grey scale and files in all industry file types.

Content can be taken from my website..... corvantshield.com

Do NOT submit if you are not willing to provide all versions as described above for the original project price.

Must use royalty-free stock photos please.

Target Market(s)

New homeowners looking for insurance to protect there mortgage payments

Industry/Entity Type

Life Insurance

Colors
f69fa3

Requirements
Must have
• Colors to be used are red, white or black.
• Need flyer in standard letter size 8.5 in. x11 in. but also in 3.5 in. x 8.5 in (Full Bleed 3.75 in by 8.75 in.) and 4.0 in. x 6.0 in. (Full Bleed 4.12 in x 6.12 in) Each design tailored to the size dimensions (So no squeezing 8.5 x 11 design into a 4.0 x 6.0 space.) All sizes to be portrait oriented. If picked as winning design, need all flyer versions in full color, also in grey scale and files in all file types.
• Do not need physical address on flyer, do need email address on flyer though - tkelwer@corvantshield.com
• So phone number should be prominent, email address and website address should also be contact area.
• If you can not agree to terms above, do not submit any designs.
• Need facebook & twitter logos somewhere in contact info area.
Nice to have
• See sample flyers I have attached.
• White background with red used as primary graphic color and black used as secondary graphic if needed.
• font to be used should similar to one used in logo.

```html
<!DOCTYPE html>
<html lang="en">
<head>
<meta charset="utf-8">
<title>Corvant Shield – Final Expense Flyer 4 x 6</title>
<link href="https://fonts.googleapis.com/css2?family=Bebas+Neue&family=Lato:wght@400;700;900&family=Montserrat:wght@300&display=swap" rel="stylesheet">
<style>
  :root{
    --canvas:#d9d9d9;
    --ink:#1e1e1e;
    --text:#333;
    --white:#fff;
    --label-grey:#cfcfcf;
  }
  *{box-sizing:border-box;margin:0;padding:0}
  html,body{width:1200px;height:1200px;overflow:hidden}
  body{background:var(--canvas);font-family:"Lato",sans-serif;position:relative}

  .size-label{
    position:absolute;top:96px;left:0;width:1200px;text-align:center;
    font-family:"Montserrat",sans-serif;font-weight:300;font-size:40px;
    color:#6a6a6a;letter-spacing:2px;
  }

  .flyer{
    --accent:#e30613;
    --box-top:#ff0a0a;
    --box-bottom:#b00d12;
    --headline-accent:#e30613;
    --photo-a:#f3f3f3;
    --photo-b:#e9dcd2;
    --photo-c:#c9a993;
    position:absolute;top:261px;width:456px;height:678px;
    background:var(--white);overflow:hidden;color:var(--text);
  }
  .flyer--color{left:115px}
  .flyer--grey{
    left:630px;
    --accent:#666;
    --box-top:#7a7a7a;
    --box-bottom:#555;
    --headline-accent:#6b6b6b;
    --photo-a:#f1f1f1;
    --photo-b:#d8d8d8;
    --photo-c:#a4a4a4;
  }

  .hero-photo{
    position:absolute;left:0;top:0;width:456px;height:270px;
    background:linear-gradient(100deg,var(--photo-a) 0%,var(--photo-a) 40%,var(--photo-b) 62%,var(--photo-c) 78%,var(--photo-b) 100%);
  }
  .shapes{position:absolute;left:0;top:0}
  .shapes .fill-white{fill:var(--white)}
  .shapes .stroke-ink{fill:none;stroke:var(--ink)}
  .shapes .stroke-accent{fill:none;stroke:var(--accent)}

  .brand{
    position:absolute;left:33px;top:50px;
    font-weight:900;font-size:17px;letter-spacing:.5px;color:var(--ink);
  }

  .headline{position:absolute;left:33px;top:0;font-family:"Bebas Neue",sans-serif;font-weight:400;color:var(--ink)}
  .headline span{position:absolute;left:0;white-space:nowrap;line-height:1}
  .headline .l1{top:138px;font-size:47px}
  .headline .l2{top:177px;font-size:42px;color:var(--headline-accent)}
  .headline .l3{top:211px;font-size:27px}

  .benefits{
    position:absolute;left:244px;top:149px;width:192px;height:240px;
    border-radius:14px;
    background:linear-gradient(180deg,var(--box-top),var(--box-bottom));
    color:var(--white);
  }
  .benefits__tab{
    position:absolute;left:-9px;top:19px;width:74px;height:14px;
    background:#333;border-radius:0 8px 8px 0;
    font-weight:700;font-size:9px;line-height:14px;padding-left:10px;
  }
  .benefits__list{
    position:absolute;left:10px;top:40px;right:6px;list-style:none;
    display:flex;flex-direction:column;gap:11px;
  }
  .benefits__list li{display:flex;gap:5px;font-weight:700;font-size:8.6px;line-height:11px}

  .check{
    flex:none;position:relative;width:8px;height:8px;margin-top:1.5px;
    border:1px solid currentColor;border-radius:50%;
  }
  .check::after{
    content:"";position:absolute;left:2px;top:1px;width:2px;height:3.5px;
    border:solid currentColor;border-width:0 1px 1px 0;transform:rotate(45deg);
  }

  .section-title{position:absolute;left:33px;font-weight:900;font-size:10.4px;color:var(--accent)}
  .section-title--intro{top:286px}
  .section-title--more{top:518px}

  .intro{
    position:absolute;left:33px;top:303px;width:182px;
    font-size:7.3px;line-height:9.6px;text-align:justify;
  }

  .rates{position:absolute;left:33px;top:366px;display:grid;grid-template-columns:121px 52px;column-gap:6px;row-gap:5px}
  .rates__label{background:var(--label-grey);font-size:8px;line-height:15px;padding-left:6px;color:#222}
  .rates__value{background:var(--accent);color:var(--white);font-weight:700;font-size:8px;line-height:15px;text-align:center}

  .body-copy{position:absolute;left:33px;top:412px;width:380px;font-size:7.3px;line-height:9.6px}
  .body-copy p{margin-bottom:9.6px}

  .specialties{position:absolute;left:33px;top:538px;display:flex;gap:16px;list-style:none;font-size:7.4px}
  .specialties li{display:flex;gap:6px;align-items:flex-start}
  .specialties .check{color:var(--accent);margin-top:0}

  .footnote{position:absolute;left:226px;top:554px;width:200px;font-size:5.3px;line-height:7px;color:#444}

  .footer-band .band{fill:url(#band-color)}
  .flyer--grey .footer-band .band{fill:url(#band-grey)}

  .call{position:absolute;left:42px;top:611px;color:var(--white);font-weight:700}
  .call__label{font-size:14px;line-height:16px}
  .call__number{font-size:22px;line-height:26px}

  .contact{position:absolute;left:221px;top:609px;list-style:none;color:var(--white);font-weight:700;font-size:8.4px}
  .contact li{display:flex;align-items:center;gap:7px;height:24px;margin-bottom:3px}
  .contact__icon{width:24px;height:24px;border:1.4px solid var(--white);border-radius:50%;display:flex;align-items:center;justify-content:center}

  .social{position:absolute;left:389px;top:650px;display:flex;gap:2px}
  .social span{width:10px;height:10px;background:var(--white);border-radius:2px}
</style>
</head>
<body>

<div class="size-label">4 x 6</div>

<svg width="0" height="0" style="position:absolute">
  <defs>
    <linearGradient id="band-color" x1="0" y1="0" x2="0" y2="1">
      <stop offset="0" stop-color="#e8121b"/><stop offset="1" stop-color="#9c1015"/>
    </linearGradient>
    <linearGradient id="band-grey" x1="0" y1="0" x2="0" y2="1">
      <stop offset="0" stop-color="#6e6e6e"/><stop offset="1" stop-color="#474747"/>
    </linearGradient>
  </defs>
</svg>

<!-- Full colour version -->
<article class="flyer flyer--color">
  <div class="hero-photo" role="img" aria-label="Photo of a smiling senior couple embracing at home"></div>
  <svg class="shapes" width="456" height="678" viewBox="0 0 456 678">
    <path class="fill-white" d="M0,0 L262,0 C228,72 128,124 0,128 Z"/>
    <path class="stroke-accent" stroke-width="4" d="M266,0 C232,74 130,127 0,131"/>
    <path class="stroke-ink" stroke-width="3" d="M272,0 C238,78 134,130 0,134"/>
    <path class="fill-white" d="M0,258 C80,268 200,272 280,260 S420,232 456,226 L456,678 L0,678 Z"/>
    <path class="stroke-ink" stroke-width="5" d="M0,245 C80,256 200,262 280,250 S420,222 456,216"/>
    <path class="stroke-accent" stroke-width="2.5" d="M0,256 C80,266 200,270 280,258 S420,230 456,224"/>
    <g class="footer-band">
      <path class="band" d="M0,616 C110,576 300,604 456,566 L456,678 L0,678 Z"/>
      <path class="stroke-ink" stroke-width="4" d="M0,608 C110,568 300,596 456,558"/>
    </g>
  </svg>

  <div class="brand">CORVANT SHIELD</div>

  <h1 class="headline"><span class="l1">Our</span><span class="l2">Plans are</span><span class="l3">Based on yours</span></h1>

  <aside class="benefits">
    <div class="benefits__tab">Benefits:</div>
    <ul class="benefits__list">
      <li><span class="check"></span>All plans we offer are state regulated</li>
      <li><span class="check"></span>Relatively low monthly premiums</li>
      <li><span class="check"></span>Premiums can never increase</li>
      <li><span class="check"></span>Your policy can never be cancelled as long as you pay your premium</li>
      <li><span class="check"></span>No medical exams</li>
      <li><span class="check"></span>Guaranteed Death Benefit</li>
      <li><span class="check"></span>Many policies we offer are Guaranteed Acceptance, "Day 1" coverage, have a child/grandchild rider and/or have an accelerated death benefit rider</li>
    </ul>
  </aside>

  <h2 class="section-title section-title--intro">Final Expense Insurance</h2>
  <p class="intro">Final Expense Insurance is a type of permanent whole life insurance insurance where the death benefit is used to cover (but not limited to) medical costs, funeral costs and other end-of-life expenses. It is a budget friendly option with a death benefit of up to $40k.</p>

  <div class="rates">
    <div class="rates__label">Monthly premiums as low as</div><div class="rates__value">$11*</div>
    <div class="rates__label">Death Benefits as high as</div><div class="rates__value">$40,000</div>
  </div>

  <div class="body-copy">
    <p>Unforeseen events and a lack of the right kind of insurance can spell trouble quickly. Contact us today, to set up a free assessment time. We will analyze your insurance needs and get you and your family the right coverage quickly at a budget friendly price.</p>
    <p>We have been helping clients in Northern Idaho/Eastern Washington prepare for the unknown.</p>
    <p>We have access to the industry's top insurance carriers so you can get the right coverage, that fits your budget.</p>
    <p>Find out how we can give you the peace of mind of knowing your family will not have a financial burden if something were to happen to you.</p>
  </div>

  <h2 class="section-title section-title--more">We Also Specialize In:</h2>
  <ul class="specialties">
    <li><span class="check"></span>Medicare Supplement Insurance (Medigap)</li>
    <li><span class="check"></span>Annuities</li>
    <li><span class="check"></span>Mortgage Protection Insurance</li>
  </ul>

  <p class="footnote">*Based on an insured that is a 65 year old, non-smoking female that has no medical conditions with a death benefit of $2k</p>

  <div class="call"><div class="call__label">Call us now:</div><div class="call__number">(208)555.0147</div></div>

  <ul class="contact">
    <li><span class="contact__icon"><svg width="12" height="9" viewBox="0 0 12 9"><rect x=".5" y=".5" width="11" height="8" fill="none" stroke="#fff"/><path d="M.5,.5 L6,5 L11.5,.5" fill="none" stroke="#fff"/></svg></span>tkelwer@corvantshield.com</li>
    <li><span class="contact__icon"><svg width="13" height="13" viewBox="0 0 13 13" fill="none" stroke="#fff"><circle cx="6.5" cy="6.5" r="5.5"/><ellipse cx="6.5" cy="6.5" rx="2.5" ry="5.5"/><path d="M1,6.5 H12"/></svg></span>corvantshield.com</li>
  </ul>
  <div class="social"><span></span><span></span></div>
</article>

<!-- Greyscale version -->
<article class="flyer flyer--grey">
  <div class="hero-photo" role="img" aria-label="Greyscale photo of a smiling senior couple embracing at home"></div>
  <svg class="shapes" width="456" height="678" viewBox="0 0 456 678">
    <path class="fill-white" d="M0,0 L262,0 C228,72 128,124 0,128 Z"/>
    <path class="stroke-accent" stroke-width="4" d="M266,0 C232,74 130,127 0,131"/>
    <path class="stroke-ink" stroke-width="3" d="M272,0 C238,78 134,130 0,134"/>
    <path class="fill-white" d="M0,258 C80,268 200,272 280,260 S420,232 456,226 L456,678 L0,678 Z"/>
    <path class="stroke-ink" stroke-width="5" d="M0,245 C80,256 200,262 280,250 S420,222 456,216"/>
    <path class="stroke-accent" stroke-width="2.5" d="M0,256 C80,266 200,270 280,258 S420,230 456,224"/>
    <g class="footer-band">
      <path class="band" d="M0,616 C110,576 300,604 456,566 L456,678 L0,678 Z"/>
      <path class="stroke-ink" stroke-width="4" d="M0,608 C110,568 300,596 456,558"/>
    </g>
  </svg>

  <div class="brand">CORVANT SHIELD</div>

  <h1 class="headline"><span class="l1">Our</span><span class="l2">Plans are</span><span class="l3">Based on yours</span></h1>

  <aside class="benefits">
    <div class="benefits__tab">Benefits:</div>
    <ul class="benefits__list">
      <li><span class="check"></span>All plans we offer are state regulated</li>
      <li><span class="check"></span>Relatively low monthly premiums</li>
      <li><span class="check"></span>Premiums can never increase</li>
      <li><span class="check"></span>Your policy can never be cancelled as long as you pay your premium</li>
      <li><span class="check"></span>No medical exams</li>
      <li><span class="check"></span>Guaranteed Death Benefit</li>
      <li><span class="check"></span>Many policies we offer are Guaranteed Acceptance, "Day 1" coverage, have a child/grandchild rider and/or have an accelerated death benefit rider</li>
    </ul>
  </aside>

  <h2 class="section-title section-title--intro">Final Expense Insurance</h2>
  <p class="intro">Final Expense Insurance is a type of permanent whole life insurance insurance where the death benefit is used to cover (but not limited to) medical costs, funeral costs and other end-of-life expenses. It is a budget friendly option with a death benefit of up to $40k.</p>

  <div class="rates">
    <div class="rates__label">Monthly premiums as low as</div><div class="rates__value">$11*</div>
    <div class="rates__label">Death Benefits as high as</div><div class="rates__value">$40,000</div>
  </div>

  <div class="body-copy">
    <p>Unforeseen events and a lack of the right kind of insurance can spell trouble quickly. Contact us today, to set up a free assessment time. We will analyze your insurance needs and get you and your family the right coverage quickly at a budget friendly price.</p>
    <p>We have been helping clients in Northern Idaho/Eastern Washington prepare for the unknown.</p>
    <p>We have access to the industry's top insurance carriers so you can get the right coverage, that fits your budget.</p>
    <p>Find out how we can give you the peace of mind of knowing your family will not have a financial burden if something were to happen to you.</p>
  </div>

  <h2 class="section-title section-title--more">We Also Specialize In:</h2>
  <ul class="specialties">
    <li><span class="check"></span>Medicare Supplement Insurance (Medigap)</li>
    <li><span class="check"></span>Annuities</li>
    <li><span class="check"></span>Mortgage Protection Insurance</li>
  </ul>

  <p class="footnote">*Based on an insured that is a 65 year old, non-smoking female that has no medical conditions with a death benefit of $2k</p>

  <div class="call"><div class="call__label">Call us now:</div><div class="call__number">(208)555.0147</div></div>

  <ul class="contact">
    <li><span class="contact__icon"><svg width="12" height="9" viewBox="0 0 12 9"><rect x=".5" y=".5" width="11" height="8" fill="none" stroke="#fff"/><path d="M.5,.5 L6,5 L11.5,.5" fill="none" stroke="#fff"/></svg></span>tkelwer@corvantshield.com</li>
    <li><span class="contact__icon"><svg width="13" height="13" viewBox="0 0 13 13" fill="none" stroke="#fff"><circle cx="6.5" cy="6.5" r="5.5"/><ellipse cx="6.5" cy="6.5" rx="2.5" ry="5.5"/><path d="M1,6.5 H12"/></svg></span>corvantshield.com</li>
  </ul>
  <div class="social"><span></span><span></span></div>
</article>

</body>
</html>
```